Dynamic Business Card for Sports Supplements Company

Hi! I'm looking for an awesome business card to match my existing sports supplement company. I have uploaded my current company logo and screenshot of the front page of my website.

I would like to have something dynamic and interesting and utilize the colors in the website - the reds and purples

The business card should be double sided and focus on a unique eye-catching design on the back and include all the relevant company info.

Most importantly, it should say somewhere: "Sign up on our website for a coupon code."

Target Market(s)

Mostly for women gym goers but it shouldn't be too feminine. It should be in keeping with the website design. It should flow and clearly be connected to it

Industry/Entity Type

Business

Contact Information for Business Card

Lorraine K. Vestal
CEO
LVestal@Quorvanexco.com
www.quorvanexco.com
555.417.3820
P.O. Box 47315
Ashgrove, Kellmont 00000

Sign up on our website for a coupon code

Font styles to use
Serif
Sans Serif
Other font styles liked:
• Novecento font family and "Quorvanex" is in AR Destine font

Requirements
Must have
• One side should be a bold Quorvanex logo design. Even just the symbol itself may be o.k. (see attached file)

```html
<!DOCTYPE html>
<html lang="en">
<head>
<meta charset="utf-8">
<title>Quorvanex Business Card</title>
<link rel="stylesheet" href="https://fonts.googleapis.com/css2?family=Figtree:wght@400;500;700;800&display=swap">
<style>
  :root {
    --backdrop: #3a3a3a;
    --card-black: #000000;
    --card-white: #ffffff;
    --brand-red: #e41e26;
    --text-light: #ffffff;
    --text-dark: #111111;
  }
  * { margin: 0; padding: 0; box-sizing: border-box; }
  html, body {
    width: 1200px;
    height: 855px;
    overflow: hidden;
    background: var(--backdrop);
    font-family: "Figtree", Arial, sans-serif;
  }
  .stage {
    position: relative;
    width: 1500px;
    height: 1069px;
    transform: scale(0.8);
    transform-origin: 0 0;
  }
  .card {
    position: absolute;
    left: 442px;
    width: 616px;
    background: var(--card-black);
    overflow: hidden;
    box-shadow: 0 4px 14px rgba(0,0,0,0.45);
  }
  /* Front side */
  .card-front { top: 171px; height: 351px; }
  .front-brand {
    position: absolute;
    left: 0; right: 0;
    top: 150px;
    text-align: center;
    color: var(--text-light);
    font-weight: 800;
    font-size: 44px;
    letter-spacing: 1px;
    text-transform: uppercase;
  }
  .front-offer {
    position: absolute;
    left: 0; right: 0;
    top: 300px;
    text-align: center;
    color: var(--text-light);
    font-size: 16px;
    font-weight: 400;
  }
  /* Back side */
  .card-back { top: 538px; height: 360px; }
  .chevron-panel { position: absolute; inset: 0; }
  .back-brand {
    position: absolute;
    left: 360px;
    width: 240px;
    top: 122px;
    text-align: center;
  }
  .back-brand-name {
    color: var(--text-dark);
    font-weight: 800;
    font-size: 30px;
    letter-spacing: 1px;
    text-transform: uppercase;
    line-height: 1;
  }
  .back-brand-tagline {
    color: var(--text-dark);
    font-size: 11.5px;
    font-weight: 500;
    letter-spacing: 0.6px;
    margin-top: 5px;
  }
  .contact-block {
    position: absolute;
    left: 32px;
    top: 148px;
    color: var(--text-light);
    font-size: 16px;
    line-height: 21px;
  }
  .person-name {
    color: var(--brand-red);
    font-size: 22px;
    font-weight: 500;
    line-height: 26px;
  }
  .person-title { margin-bottom: 14px; }
  .address { margin-bottom: 15px; }
  .contact-line { display: flex; align-items: center; gap: 6px; }
  .contact-icon { width: 14px; height: 14px; fill: var(--brand-red); flex: none; }
</style>
</head>
<body>
<div class="stage">

  <section class="card card-front">
    <div class="front-brand">Quorvanex</div>
    <p class="front-offer">Sign up on our website for a coupon code</p>
  </section>

  <section class="card card-back">
    <svg class="chevron-panel" viewBox="0 0 616 360" width="616" height="360">
      <polygon points="170,0 616,0 616,188 482,338" fill="var(--card-white)"/>
      <polyline points="179,0 482,327 616,177" fill="none" stroke="var(--brand-red)" stroke-width="5"/>
    </svg>

    <div class="back-brand">
      <div class="back-brand-name">Quorvanex</div>
      <div class="back-brand-tagline">BUILT FOR STRONGER DAYS</div>
    </div>

    <div class="contact-block">
      <div class="person-name">Lorraine K. Vestal</div>
      <div class="person-title">CEO</div>
      <div class="address">P.O. Box 47315<br>Ashgrove, Kellmont 00000</div>
      <div class="contact-line">
        <svg class="contact-icon" viewBox="0 0 16 16"><path d="M3 1l3 3-1.5 2c1 2 2.5 3.5 4.5 4.5L11 9l3 3-2 2.5C6 14 2 10 1.5 3z"/></svg>
        <span>555.417.3820</span>
      </div>
      <div class="contact-line">
        <svg class="contact-icon" viewBox="0 0 16 16"><path d="M1 4h14v9H1z M1 4l7 5 7-5" stroke="#000" stroke-width="1"/></svg>
        <span>LVestal@Quorvanexco.com</span>
      </div>
      <div class="contact-line">
        <svg class="contact-icon" viewBox="0 0 16 16"><circle cx="8" cy="8" r="6.5" fill="none" stroke="var(--brand-red)" stroke-width="1.4"/><path d="M1.5 8h13M8 1.5c-3 3.5-3 9.5 0 13M8 1.5c3 3.5 3 9.5 0 13" fill="none" stroke="var(--brand-red)" stroke-width="1.2"/></svg>
        <span>www.quorvanexco.com</span>
      </div>
    </div>
  </section>

</div>
</body>
</html>
```